Modern looking signage for dental office.

Exterior signage for passing cars
Updates
Need extra days to review
Target Market(s)
Cars passing by
Font styles to use
Sans Serif
Colors
3276b5
Requirements
Must have
- Logo
- OPEN ON SUTURDAY AND SUNDAY
- NIGHT CLINIC AVAILABLE
- PLEASE USE THE FONT TYPE IN FILE 4 UPLOADED BELOW.
- (847) 302-7469
- Modern looking

```html
<!DOCTYPE html>
<html lang="en">
<head>
<meta charset="utf-8">
<title>Crestline Dental – Weekend &amp; Night Clinic Sign</title>
<link href="https://fonts.googleapis.com/css2?family=Lato:wght@300;400;700;900&family=Roboto+Condensed:wght@300;400&display=swap" rel="stylesheet">
<style>
  :root {
    --teal: #0a87a0;
    --charcoal: #464446;
    --slate: #636466;
    --white: #ffffff;
  }
  html, body {
    margin: 0;
    padding: 0;
    width: 1200px;
    height: 1200px;
    overflow: hidden;
    background: var(--white);
  }
  .sign {
    position: relative;
    width: 1200px;
    height: 1200px;
    font-family: "Lato", sans-serif;
    background: var(--white);
    overflow: hidden;
  }
  .header-curves {
    position: absolute;
    left: 0;
    top: 0;
    width: 1200px;
    height: 440px;
  }
  .brand {
    position: absolute;
    left: 150px;
    top: 72px;
    display: flex;
    align-items: center;
    gap: 32px;
  }
  .brand-dot {
    width: 186px;
    height: 186px;
    border: 3px solid var(--charcoal);
    border-radius: 50%;
    box-sizing: border-box;
    flex: none;
  }
  .brand-text { display: flex; flex-direction: column; }
  .brand-name {
    font-family: "Lato", sans-serif;
    font-weight: 300;
    font-size: 104px;
    line-height: 1;
    color: var(--charcoal);
    letter-spacing: 1px;
    white-space: nowrap;
    margin: 0;
  }
  .brand-tagline {
    font-family: "Roboto Condensed", sans-serif;
    font-weight: 400;
    font-size: 40px;
    color: var(--charcoal);
    margin: 14px 0 0 56px;
    white-space: nowrap;
  }
  .open-banner {
    position: absolute;
    left: 62px;
    top: 495px;
    width: 1076px;
    height: 188px;
    background: var(--teal);
    color: var(--white);
    display: flex;
    align-items: center;
  }
  .open-word {
    font-weight: 900;
    font-size: 192px;
    line-height: 1;
    margin-left: 14px;
    letter-spacing: -4px;
  }
  .open-days {
    margin-left: 26px;
    font-weight: 400;
    font-size: 78px;
    line-height: 82px;
    white-space: nowrap;
  }
  .night-bar {
    position: absolute;
    left: 62px;
    top: 714px;
    width: 1076px;
    height: 74px;
    background: var(--slate);
    color: var(--white);
    font-weight: 700;
    font-size: 49px;
    display: flex;
    align-items: center;
    justify-content: center;
    white-space: nowrap;
  }
  .night-hours {
    background: var(--teal);
    height: 74px;
    display: flex;
    align-items: center;
    padding: 0 8px;
    margin: 0 10px;
  }
  .contact {
    position: absolute;
    left: 0;
    top: 835px;
    width: 1200px;
    height: 365px;
    background: var(--slate);
  }
  .contact-frame {
    position: absolute;
    left: 0;
    top: 0;
    width: 1200px;
    height: 300px;
  }
  .phone-number {
    position: absolute;
    left: 0;
    top: 138px;
    width: 1200px;
    text-align: center;
    color: var(--white);
    font-weight: 700;
    font-size: 156px;
    line-height: 1;
    letter-spacing: 1px;
  }
  .website {
    position: absolute;
    left: 0;
    top: 306px;
    width: 1200px;
    text-align: center;
    color: var(--white);
    font-weight: 400;
    font-size: 31px;
  }
</style>
</head>
<body>
  <main class="sign">
    <svg class="header-curves" viewBox="0 0 1200 440" aria-hidden="true">
      <path d="M0 136 C 200 340, 450 420, 620 408 C 850 400, 1050 330, 1200 226" fill="none" stroke="#464446" stroke-width="3"/>
      <path d="M0 198 C 200 350, 420 415, 600 412 C 820 410, 1050 310, 1200 186" fill="none" stroke="#0a87a0" stroke-width="3"/>
    </svg>

    <header class="brand">
      <div class="brand-dot"></div>
      <div class="brand-text">
        <h1 class="brand-name">CRESTLINE</h1>
        <p class="brand-tagline">MODERN GENERAL DENTISTRY</p>
      </div>
    </header>

    <section class="open-banner">
      <span class="open-word">OPEN</span>
      <span class="open-days">on SATURDAY<br>and SUNDAY</span>
    </section>

    <section class="night-bar">
      Night clinic from<span class="night-hours">5pm to 10pm</span>available
    </section>

    <footer class="contact">
      <svg class="contact-frame" viewBox="0 0 1200 300" aria-hidden="true">
        <path d="M462 126 H112 A40 40 0 0 0 72 166 V245 A40 40 0 0 0 112 285 H1088 A40 40 0 0 0 1128 245 V166 A40 40 0 0 0 1088 126 H598" fill="none" stroke="#ffffff" stroke-width="4"/>
        <circle cx="598" cy="64" r="59" fill="none" stroke="#ffffff" stroke-width="4"/>
        <path d="M575 38 C 568 44, 566 54, 572 66 C 580 82, 592 94, 608 101 C 618 105, 626 102, 631 96 L 620 84 C 616 88, 611 89, 606 86 C 597 80, 590 72, 586 63 C 584 58, 585 54, 589 51 Z" fill="none" stroke="#ffffff" stroke-width="5" stroke-linejoin="round"/>
        <path d="M604 46 A22 22 0 0 1 624 66" fill="none" stroke="#ffffff" stroke-width="4" stroke-linecap="round"/>
        <path d="M606 34 A34 34 0 0 1 636 64" fill="none" stroke="#ffffff" stroke-width="4" stroke-linecap="round"/>
        <path d="M609 22 A46 46 0 0 1 648 62" fill="none" stroke="#ffffff" stroke-width="4" stroke-linecap="round"/>
      </svg>
      <div class="phone-number">847 302 7469</div>
      <div class="website">www.crestlinedentalclinic.com</div>
    </footer>
  </main>
</body>
</html>
```